Consumer and commercial IOT solutions (Internet Of Things)

We are a startup and are looking for business cards with logo. The logo will appear on all of our media as well as our ecommerce site and social sites that have yet to be developed. We want to present a fresh face on a high tech company that innovates at every turn. You can read about our solutions on our information only web site www.plonaxhub.net - We have some wording we would like used on our business cards but there is no place for this except for here. The company name is "RM Industrial IOT" I have some samples of logos I am interested in seeing but I will let your team make the initial presentations

```html
<!DOCTYPE html>
<html lang="en">
<head>
<meta charset="utf-8">
<title>RM Industrial IOT – Business Card</title>
<link href="https://fonts.googleapis.com/css2?family=Arimo:wght@400;700&display=swap" rel="stylesheet">
<style>
  :root {
    --stage: #1f1f1f;
    --card-white: #ffffff;
    --brand-orange: #ec8a32;
    --ink: #1b1b1b;
    --rule: #8a8a8a;
  }
  * { box-sizing: border-box; margin: 0; padding: 0; }
  html, body {
    width: 1200px;
    height: 1108px;
    overflow: hidden;
    background: var(--stage);
    font-family: "Arimo", Arial, sans-serif;
  }
  .stage {
    position: relative;
    width: 1200px;
    height: 1108px;
    display: flex;
    align-items: center;
    justify-content: center;
    gap: 90px;
  }
  .card {
    width: 380px;
    height: 640px;
    border-radius: 24px;
    position: relative;
    overflow: hidden;
  }
  .card-front {
    background: var(--card-white);
    color: var(--ink);
    display: flex;
    flex-direction: column;
    align-items: center;
    padding-top: 60px;
    text-align: center;
  }
  .brand-circle {
    width: 130px;
    height: 130px;
    border-radius: 50%;
    border: 9px solid var(--brand-orange);
  }
  .brand-name {
    margin-top: 26px;
    font-weight: 700;
    font-size: 34px;
    letter-spacing: 1px;
    line-height: 1.15;
    color: var(--ink);
    white-space: nowrap;
  }
  .brand-rule {
    width: 250px;
    height: 2px;
    background: var(--ink);
    margin-top: 14px;
  }
  .person-name {
    margin-top: 30px;
    font-weight: 700;
    font-size: 27px;
    letter-spacing: 1px;
    color: var(--brand-orange);
  }
  .person-title {
    font-size: 17px;
    margin-top: 2px;
  }
  .icon-row {
    display: flex;
    align-items: center;
    gap: 8px;
    margin-top: 20px;
    width: 190px;
  }
  .icon-row .line {
    flex: 1;
    height: 1px;
    background: var(--rule);
  }
  .icon {
    width: 27px;
    height: 27px;
    background: var(--brand-orange);
    border-radius: 4px;
    display: flex;
    align-items: center;
    justify-content: center;
  }
  .contact {
    margin-top: 14px;
    font-size: 18px;
    line-height: 1.45;
  }
  .contact .accent { color: var(--brand-orange); }
  .contact-rule {
    width: 200px;
    height: 1px;
    background: var(--rule);
    margin-top: 10px;
  }
  .address {
    margin-top: 12px;
    font-size: 18px;
    line-height: 1.45;
  }
  .card-back {
    background: linear-gradient(160deg, #f09238 0%, #e8862e 55%, #df7c26 100%);
  }
  .back-texture {
    position: absolute;
    inset: 0;
  }
  .back-brand {
    position: absolute;
    left: 0;
    right: 0;
    bottom: 140px;
    text-align: center;
    color: #ffffff;
    font-weight: 700;
    font-size: 15px;
    letter-spacing: 1px;
  }
</style>
</head>
<body>
<main class="stage">
  <section class="card card-front" aria-label="Business card front">
    <div class="brand-circle" aria-hidden="true"></div>
    <div class="brand-name">RM INDUSTRIAL IOT</div>
    <div class="brand-rule"></div>
    <h1 class="person-name">DANIEL HARPER</h1>
    <p class="person-title">Managing Director</p>
    <div class="icon-row">
      <span class="line"></span>
      <span class="icon" aria-label="Phone">
        <svg width="17" height="17" viewBox="0 0 24 24"><path fill="#fff" d="M6.6 10.8a15 15 0 0 0 6.6 6.6l2.2-2.2c.3-.3.7-.4 1-.2 1.1.4 2.3.6 3.6.6.6 0 1 .4 1 1V20c0 .6-.4 1-1 1A17 17 0 0 1 3 4c0-.6.4-1 1-1h3.5c.6 0 1 .4 1 1 0 1.3.2 2.5.6 3.6.1.3 0 .7-.2 1z"/></svg>
      </span>
      <span class="icon" aria-label="Email">
        <svg width="17" height="17" viewBox="0 0 24 24"><rect x="3" y="6" width="18" height="12" fill="none" stroke="#fff" stroke-width="2"/><path d="M3 6l9 7 9-7" fill="none" stroke="#fff" stroke-width="2"/></svg>
      </span>
      <span class="icon" aria-label="Web">
        <svg width="17" height="17" viewBox="0 0 24 24"><circle cx="12" cy="12" r="9" fill="none" stroke="#fff" stroke-width="2"/><path d="M3 12h18M12 3c3 3 3 15 0 18M12 3c-3 3-3 15 0 18" fill="none" stroke="#fff" stroke-width="1.5"/></svg>
      </span>
      <span class="line"></span>
    </div>
    <div class="contact">
      <p>044-718 302 645</p>
      <p>info@plonaxhub.net</p>
      <p>www.<span class="accent">plonaxhub</span>.net</p>
    </div>
    <div class="contact-rule"></div>
    <div class="address">
      <p>58 Harbor Works Road</p>
      <p>60418, Northland</p>
    </div>
  </section>

  <section class="card card-back" aria-label="Business card back">
    <div class="back-texture" role="img" aria-label="Repeating embossed gold brand-mark pattern across the orange card back"></div>
    <div class="back-brand">RM INDUSTRIAL IOT</div>
  </section>
</main>
</body>
</html>
```